Verlindo Magician

I want the business card for my business to give to people who watch that later I will be employed to show magic here is my website http://www.verlindoillusions.example/I want the interesting design , i am very opened for formal and informal, I watch a lot of design so don't stick to the common shape and form but i hope it can also be produced the thing to write on will be the same as in picture that i will upload , i also will upload the logo for you that so can be easy to useDenis CostilleMagicianMAGICIAN BALSAMO 17 rue des Tilleuls - 25000 BESANÇON contact@verlindoillusions.example tel. 0381 946 157 tel. 0674 219 503

```html
<!DOCTYPE html>
<html lang="fr">
<head>
<meta charset="utf-8">
<title>Verlindo Magicien – Cartes de visite</title>
<link rel="stylesheet" href="https://fonts.googleapis.com/css2?family=Jost:wght@300;400;500&display=swap">
<style>
  :root {
    --backdrop: #2b2b2b;
    --card: #ffffff;
    --card-shade: #f3f3f3;
    --ink: #111111;
    --ink-soft: #2a2a2a;
    --rule: #1a1a1a;
    --portrait-dark: #0d0d0d;
    --portrait-mid: #3a3a3a;
  }
  * { margin: 0; padding: 0; box-sizing: border-box; }
  html, body {
    width: 1200px; height: 895px; overflow: hidden;
    background: var(--backdrop);
    font-family: "Jost", "Futura", sans-serif;
    color: var(--ink);
  }
  .sheet {
    width: 1200px; height: 895px;
    display: flex; flex-direction: column;
    align-items: center; justify-content: center; gap: 40px;
  }
  .card {
    position: relative;
    width: 700px; height: 400px;
    background: linear-gradient(160deg, var(--card) 0%, var(--card) 60%, var(--card-shade) 100%);
    box-shadow: 0 10px 30px rgba(0,0,0,.45);
  }
  .portrait {
    position: absolute;
    background: radial-gradient(ellipse at 50% 30%, var(--portrait-mid) 0%, var(--portrait-dark) 70%);
    border-radius: 48% 48% 18% 18% / 40% 40% 12% 12%;
  }
  /* front */
  .card--front .portrait { left: 278px; top: 50px; width: 144px; height: 190px; }
  .brand {
    position: absolute; left: 0; right: 0; top: 252px;
    text-align: center; font-weight: 300; color: var(--ink);
    letter-spacing: 0.08em; line-height: 1;
  }
  .brand__name { display: block; font-size: 38px; }
  .brand__sub { display: block; font-size: 11px; letter-spacing: 0.25em; margin-top: 8px; }
  /* back */
  .card--back .portrait { left: 110px; top: 120px; width: 170px; height: 200px; }
  .divider {
    position: absolute; left: 350px; top: 100px;
    width: 1.5px; height: 220px; background: var(--rule);
  }
  .details { position: absolute; left: 376px; top: 92px; }
  .details__name { font-size: 27px; font-weight: 500; letter-spacing: 0.02em; line-height: 1; }
  .details__role { font-size: 14px; font-weight: 400; letter-spacing: 0.06em; margin-top: 4px; }
  .details__company { font-size: 14px; letter-spacing: 0.05em; margin-top: 20px; }
  .details__address { font-size: 14px; margin-top: 2px; }
  .contact-list { list-style: none; margin-top: 18px; }
  .contact-list li {
    display: flex; align-items: center; gap: 10px;
    font-size: 14.5px; color: var(--ink-soft); line-height: 1.55;
  }
  .contact-list svg { width: 11px; height: 11px; fill: var(--ink); flex: none; }
</style>
</head>
<body>
<main class="sheet">
  <section class="card card--front">
    <div class="portrait" role="img" aria-label="Illustration en noir et blanc du magicien tenant une carte à jouer"></div>
    <p class="brand">
      <span class="brand__name">VERLINDO</span>
      <span class="brand__sub">MAGICIEN</span>
    </p>
  </section>

  <section class="card card--back">
    <div class="portrait" role="img" aria-label="Illustration en noir et blanc du magicien tenant une carte à jouer"></div>
    <div class="divider"></div>
    <div class="details">
      <h1 class="details__name">MARC RAVOULET</h1>
      <p class="details__role">MAGICIEN</p>
      <p class="details__company">VERLINDO MAGICIEN</p>
      <p class="details__address">17 rue des Tilleuls - 25000 BESANÇON</p>
      <ul class="contact-list">
        <li><svg viewBox="0 0 12 12" aria-hidden="true"><path d="M2.5 0.5l2 2-1 1.5c.8 1.6 2 2.8 3.5 3.5l1.5-1 2 2-1.5 2C4.5 11.8.2 7.5.5 1.5z"/></svg>0381 946 157</li>
        <li><svg viewBox="0 0 12 12" aria-hidden="true"><path d="M2.5 0.5l2 2-1 1.5c.8 1.6 2 2.8 3.5 3.5l1.5-1 2 2-1.5 2C4.5 11.8.2 7.5.5 1.5z"/></svg>0674 219 503</li>
        <li><svg viewBox="0 0 12 12" aria-hidden="true"><path d="M0 2h12v1L6 7 0 3z M0 4.5l6 4 6-4V10H0z"/></svg>contact@verlindoillusions.example</li>
        <li><svg viewBox="0 0 12 12" aria-hidden="true"><path d="M6 0a6 6 0 1 0 0 12A6 6 0 0 0 6 0zm0 1.2c.8 0 1.6 1.9 1.7 4.2H4.3C4.4 3.1 5.2 1.2 6 1.2zM1.2 6.6h2.1c.1 1.6.5 3 1 3.9A4.8 4.8 0 0 1 1.2 6.6zm0-1.2a4.8 4.8 0 0 1 3.1-3.9c-.5.9-.9 2.3-1 3.9zm4.8 5.4c-.8 0-1.6-1.9-1.7-4.2h3.4c-.1 2.3-.9 4.2-1.7 4.2zm1.7-.3c.5-.9.9-2.3 1-3.9h2.1a4.8 4.8 0 0 1-3.1 3.9zm1-5.1c-.1-1.6-.5-3-1-3.9a4.8 4.8 0 0 1 3.1 3.9z"/></svg>www.verlindoillusions.example</li>
      </ul>
    </div>
  </section>
</main>
</body>
</html>
```